Website Design for The Elder Nook

Please design and code a new website.
Here are the sites I like best:
http://www.voyaglint.com/alternate/
http://www.wheelgiftbay.org
Please make it similar but look at the competitor site (below) for images and wording. This is NOT a car donation site. It's a senior lead placement site like https://www.kinhavenfinder.com. I just like this sites above as a lead generation sites.
Competitor site:
https://www.kinhavenfinder.com (use ideas / verbiage from this site)
Updates
Competitor site:
Coding
Coded - Design and coding required
Number of Pages Required
1 page
Look and feel
Each slider illustrates characteristics of the customer's brand and the style your logo design should communicate.

```html
<!DOCTYPE html>
<html lang="en">
<head>
<meta charset="utf-8">
<title>The Elder Nook</title>
<link href="https://fonts.googleapis.com/css2?family=Raleway:wght@600;700;800&family=Open+Sans:ital,wght@0,400;0,600;0,700;1,400&display=swap" rel="stylesheet">
<style>
:root{
  --blue:#0b72ae;
  --blue-dark:#075d8f;
  --orange:#ee8422;
  --orange-soft:#f0953a;
  --text:#333;
  --muted:#666;
  --line:#d8d8d8;
  --white:#fff;
  --gold:#d4b106;
}
*{margin:0;padding:0;box-sizing:border-box}
html,body{width:1200px;height:3244px;overflow:hidden;background:var(--white)}
body{font-family:'Open Sans',sans-serif;color:var(--text);position:relative}
.abs{position:absolute}
h1,h2,h3{font-family:'Raleway',sans-serif}

/* header */
.brand{left:112px;top:34px;display:flex;align-items:center;gap:10px;font-family:'Raleway',sans-serif;font-weight:700;font-size:25px;color:var(--blue)}
.brand-dot{width:38px;height:38px;border:4px solid var(--blue);border-radius:50%}
.hotline{right:111px;top:18px;display:flex;align-items:center;gap:8px;font-size:14px;color:#444}
.hotline-icon{width:32px;height:32px;border:1px solid #bbb;border-radius:50%;display:flex;align-items:center;justify-content:center}
.hotline strong{color:var(--blue);font-size:20px;font-weight:700}
.main-nav{right:111px;top:66px;display:flex;gap:19px;font-size:15.5px;font-weight:600;color:#333}
.rule{left:0;width:1200px;height:1px;background:var(--line)}
.cities{left:105px;top:112px;display:flex;gap:19px;font-size:14.5px;color:#555}

/* hero */
.hero{left:0;top:145px;width:1200px;height:640px;overflow:hidden}
.hero-photo{position:absolute;inset:0;background:linear-gradient(90deg,#c9cbc6 0%,#dcdcd6 35%,#a9a7a1 60%,#86817a 80%,#6f6a63 100%)}
.hero-title{left:112px;top:84px;font-family:'Raleway',sans-serif;font-weight:800;font-size:51px;color:var(--white)}
.hero-call{left:179px;top:154px;font-size:20px;color:var(--white);font-weight:600}
.hero-call b{font-size:25px}
.search-card{left:152px;top:214px;width:388px;height:227px;background:rgba(110,110,110,.55);border-radius:5px;text-align:center;padding-top:26px}
.search-card h3{font-family:'Open Sans',sans-serif;font-weight:600;font-size:21px;color:var(--white)}
.field{display:flex;align-items:center;gap:8px;background:var(--white);color:#666;font-size:14.5px;padding:0 18px}
.search-card .field{margin:18px auto 0;width:293px;height:46px}
.btn-orange{display:block;margin:15px auto 0;width:284px;height:56px;border-radius:28px;background:var(--orange);color:var(--white);font-weight:700;font-size:16px;line-height:56px;letter-spacing:.3px}
.dots{left:566px;top:527px;display:flex;gap:5px}
.dots span{width:14px;height:14px;border:2px solid var(--white);border-radius:50%}
.dots span:first-child{background:var(--white)}

/* welcome */
.section-title{width:1200px;left:0;text-align:center;font-weight:800;font-size:39px;color:var(--blue)}
.intro{left:225px;top:918px;width:750px;text-align:center;font-size:14.5px;line-height:29px;color:var(--muted)}
.feature{width:220px;text-align:center;top:1042px}
.ring{width:154px;height:154px;margin:0 auto;border:2px solid var(--blue);border-radius:50%;display:flex;align-items:center;justify-content:center}
.ring-inner{width:134px;height:134px;border:5px solid var(--blue);border-radius:50%;display:flex;align-items:center;justify-content:center}
.feature h3{font-family:'Open Sans',sans-serif;font-weight:600;font-size:19px;margin-top:18px;color:#333}
.feature p{font-size:13.8px;line-height:26px;color:var(--muted);margin-top:14px}

/* why */
.why{left:0;top:1420px;width:1200px;height:564px;background:var(--blue)}
.why h2{position:absolute;left:112px;top:80px;font-weight:800;font-size:39px;color:var(--white)}
.why-lead{position:absolute;left:112px;top:142px;width:430px;font-size:14px;line-height:27px;color:var(--white)}
.why-item{position:absolute;left:112px;display:flex;align-items:center;gap:25px;font-family:'Raleway',sans-serif;font-weight:600;font-size:19.5px;line-height:28px;color:var(--white)}
.why-item .disc{width:70px;height:70px;border-radius:50%;background:var(--white);display:flex;align-items:center;justify-content:center;flex:none}
.why-photo{position:absolute;left:600px;top:72px;width:488px;height:422px;border-radius:26px;border:5px solid var(--white);background:linear-gradient(135deg,#eeeae4 0%,#d9d2c8 45%,#b7aca0 70%,#4b4a52 100%)}

/* testimonials */
.stars{left:0;width:1200px;top:2175px;display:flex;justify-content:center;gap:2px}
.quote{left:220px;top:2220px;width:760px;text-align:center;font-style:italic;font-size:15px;line-height:31px;color:#555}
.avatar{border-radius:50%;background:linear-gradient(180deg,#e8e8ea,#a9acb5)}
.person{left:0;width:1200px;text-align:center}

/* advisor */
.advisor{left:0;top:2584px;width:1200px;height:660px;background:linear-gradient(180deg,var(--orange-soft),#ef8d2c)}
.advisor h2{position:absolute;left:0;width:1200px;top:60px;text-align:center;font-weight:800;font-size:39px;color:var(--white)}
.advisor .field{position:absolute;left:237px;top:144px;width:583px;height:57px;font-size:15px}
.btn-blue{position:absolute;left:820px;top:144px;width:143px;height:57px;background:var(--blue);color:var(--white);font-weight:700;font-size:17px;text-align:center;line-height:57px;letter-spacing:.5px}
.social{left:0;width:1200px;top:2984px;display:flex;justify-content:center;gap:8px}
.social span{width:50px;height:50px;border:1px solid #999;border-radius:50%;background:var(--white)}
.contact{left:0;width:1200px;top:3070px;text-align:center;font-size:14.5px;color:#666;display:flex;justify-content:center;align-items:center;gap:8px}
.links{left:0;width:1200px;top:3117px;display:flex;justify-content:center;gap:18px;font-size:14.5px;color:#666}
.copy{left:0;width:1200px;top:3160px;text-align:center;font-size:14.5px;color:#666}
</style>
</head>
<body>

<header>
  <div class="abs brand"><span class="brand-dot"></span>The Elder Nook</div>
  <div class="abs hotline">
    <span class="hotline-icon"><svg width="14" height="14" viewBox="0 0 24 24"><path d="M6.6 10.8a15 15 0 0 0 6.6 6.6l2.2-2.2a1 1 0 0 1 1-.25 11.4 11.4 0 0 0 3.6.57 1 1 0 0 1 1 1V20a1 1 0 0 1-1 1A17 17 0 0 1 3 4a1 1 0 0 1 1-1h3.5a1 1 0 0 1 1 1c0 1.25.2 2.45.57 3.57a1 1 0 0 1-.25 1z" fill="#ee8422"/></svg></span>
    Talk to a local advisor for FREE <strong>1 800 555 0142</strong>
  </div>
  <nav class="abs main-nav"><span>Assisted Living</span><span>Memory Care</span><span>Nursing Homes</span><span>More Living Options</span><span>Planning &amp; Advice</span></nav>
  <div class="abs rule" style="top:104px"></div>
  <nav class="abs cities"><span>New York</span><span>Los Angeles</span><span>Chicago</span><span>Dallas</span><span>Houston</span><span>Philadelphia</span><span>Miami</span><span>Atlanta</span><span>Boston</span><span>San Jose</span><span>Phoenix</span><span>Seattle</span><span>Minneapolis</span></nav>
</header>

<section class="abs hero">
  <div class="hero-photo" role="img" aria-label="Smiling senior man sitting in a bright living room"></div>
  <svg class="abs" style="left:0;top:0" width="1200" height="640" viewBox="0 0 1200 640">
    <path d="M0,480 Q600,760 1200,480 L1200,640 L0,640 Z" fill="#fff"/>
    <path d="M0,480 Q600,760 1200,480" fill="none" stroke="#ee8422" stroke-width="10"/>
  </svg>
  <h1 class="abs hero-title">THE ELDER NOOK</h1>
  <p class="abs hero-call">Need help? Call <b>1 800 555 0142</b></p>
  <div class="abs search-card">
    <h3>Find Senior Living Near You</h3>
    <div class="field"><svg width="11" height="15" viewBox="0 0 12 16"><path d="M6 0a6 6 0 0 0-6 6c0 4.5 6 10 6 10s6-5.5 6-10a6 6 0 0 0-6-6zm0 8.5A2.5 2.5 0 1 1 6 3.5a2.5 2.5 0 0 1 0 5z" fill="#666"/></svg>Enter City or Postal Code</div>
    <span class="btn-orange">START YOUR SEARCH</span>
  </div>
  <div class="abs dots"><span></span><span></span><span></span><span></span></div>
</section>

<section>
  <h2 class="abs section-title" style="top:852px">WELCOME TO THE ELDER NOOK</h2>
  <p class="abs intro">Ut enim ad minima veniam, quis nostrum exercitationem ullam corporis suscipit laboriosam, nisi ut aliquid ex eacommodi consequ autem vel eum iure reprehenderit qui in ea voluptate velit esse quam nihil molestiae consequatur, vel illum qui dolorem eum fugiat quo voluptas nulla pari.</p>

  <div class="abs feature" style="left:99px">
    <div class="ring"><div class="ring-inner"><svg width="50" height="52" viewBox="0 0 50 52"><rect x="2" y="8" width="46" height="42" rx="3" fill="none" stroke="#ee8422" stroke-width="4"/><rect x="2" y="8" width="46" height="10" fill="#ee8422"/><rect x="12" y="2" width="5" height="10" fill="#ee8422"/><rect x="33" y="2" width="5" height="10" fill="#ee8422"/><g fill="#ee8422"><rect x="9" y="23" width="7" height="6"/><rect x="19" y="23" width="7" height="6"/><rect x="29" y="23" width="7" height="6"/><rect x="39" y="23" width="5" height="6"/><rect x="9" y="33" width="7" height="6"/><rect x="19" y="33" width="7" height="6"/><rect x="29" y="33" width="7" height="6"/><rect x="39" y="33" width="5" height="6"/></g></svg></div></div>
    <h3>Help scheduling tours</h3>
    <p>Nemo enim ipsam voluptatem quia voluptas sit aspernatur aut odit aut fugit ostru.</p>
  </div>
  <div class="abs feature" style="left:358px">
    <div class="ring"><div class="ring-inner"><svg width="58" height="46" viewBox="0 0 58 46"><path d="M2 4v16l24 24 20-20L22 0H6a4 4 0 0 0-4 4z" fill="#ee8422"/><circle cx="12" cy="10" r="4" fill="#fff"/><path d="M30 0l24 24-20 20" fill="none" stroke="#ee8422" stroke-width="4"/></svg></div></div>
    <h3>Full details and pricing</h3>
    <p>Nemo enim ipsam voluptatem quia voluptas sit aspernatur aut odit aut fugit ostru.</p>
  </div>
  <div class="abs feature" style="left:617px">
    <div class="ring"><div class="ring-inner"><svg width="42" height="46" viewBox="0 0 42 46"><circle cx="21" cy="12" r="11" fill="#ee8422"/><path d="M0 46v-6a14 14 0 0 1 14-14h14a14 14 0 0 1 14 14v6z" fill="#ee8422"/></svg></div></div>
    <h3>Dedicated local advisor</h3>
    <p>Nemo enim ipsam voluptatem quia voluptas sit aspernatur aut odit aut fugit ostru.</p>
  </div>
  <div class="abs feature" style="left:876px">
    <div class="ring"><div class="ring-inner"><svg width="44" height="54" viewBox="0 0 44 54"><path d="M0 0h30l14 14v40H0z" fill="#ee8422"/><path d="M30 0v14h14" fill="#f7c18f"/><g fill="#fff"><rect x="9" y="24" width="26" height="4"/><rect x="9" y="32" width="26" height="4"/><rect x="9" y="40" width="26" height="4"/></g></svg></div></div>
    <h3>Hand-picked list</h3>
    <p>Nemo enim ipsam voluptatem quia voluptas sit aspernatur aut odit aut fugit ostru.</p>
  </div>
</section>

<section class="abs why">
  <h2>WHY CHOOSE US</h2>
  <p class="why-lead">Nemo enim ipsam voluptatem quia voluptas sit aspernatur aut odit aut fugit, sed quia consequuntur magni dolor.</p>
  <div class="why-item" style="top:227px"><span class="disc"><svg width="34" height="28" viewBox="0 0 34 28"><ellipse cx="14" cy="11" rx="12" ry="9" fill="none" stroke="#ee8422" stroke-width="3"/><path d="M6 18l-3 7 8-4" fill="#ee8422"/><path d="M26 10a10 8 0 0 1 0 15l4 3-9-2" fill="none" stroke="#ee8422" stroke-width="3"/></svg></span>Advice tailored to your<br>unique situation</div>
  <div class="why-item" style="top:313px"><span class="disc"><svg width="30" height="30" viewBox="0 0 30 30"><circle cx="15" cy="15" r="12" fill="none" stroke="#ee8422" stroke-width="3.5"/><path d="M15 8v8h-6" fill="none" stroke="#ee8422" stroke-width="3"/></svg></span>Time saving know-how<br>and resources</div>
  <div class="why-item" style="top:398px"><span class="disc"><svg width="22" height="30" viewBox="0 0 12 16"><path d="M6 0a6 6 0 0 0-6 6c0 4.5 6 10 6 10s6-5.5 6-10a6 6 0 0 0-6-6zm0 8.5A2.5 2.5 0 1 1 6 3.5a2.5 2.5 0 0 1 0 5z" fill="#ee8422"/></svg></span>Insider's tips for the area<br>near you</div>
  <div class="why-photo" role="img" aria-label="Senior couple laughing together outdoors in winter clothes"></div>
</section>

<section>
  <h2 class="abs section-title" style="top:2090px">TESTIMONIALS</h2>
  <div class="abs stars">
    <svg width="104" height="20" viewBox="0 0 104 20"><g fill="#d4b106"><path id="st" d="M10 1l2.7 6 6.3.6-4.8 4.2 1.4 6.4L10 15l-5.6 3.2 1.4-6.4L1 7.6 7.3 7z"/><use href="#st" x="21"/><use href="#st" x="42"/><use href="#st" x="63"/></g><use href="#st" x="84" fill="none" stroke="#d4b106" stroke-width="1.3"/></svg>
  </div>
  <p class="abs quote">Nemo enim ipsam voluptatem quia voluptas sit aspernatur aut odit aut fugit, sed quia consequuntur magni dolores eos qui ratione voluptatem eque porro quisquam est, qui dolorem ipsum quia dt</p>
  <div class="abs avatar" style="left:446px;top:2316px;width:84px;height:84px;opacity:.8" role="img" aria-label="Portrait of a client"></div>
  <div class="abs avatar" style="left:550px;top:2308px;width:100px;height:100px;background:linear-gradient(180deg,#cfe3ef,#4d7fa8)" role="img" aria-label="Portrait of Martin Hale"></div>
  <div class="abs avatar" style="left:668px;top:2316px;width:84px;height:84px;opacity:.8;background:linear-gradient(180deg,#e8e8ee,#8b86c2)" role="img" aria-label="Portrait of a client"></div>
  <p class="abs person" style="top:2438px;font-size:17px;font-weight:600;color:#333">MARTIN HALE</p>
  <p class="abs person" style="top:2468px;font-size:14px;color:#555">Eiusmod tempor incid</p>
</section>

<section class="abs advisor">
  <div class="abs" style="inset:0;background:linear-gradient(90deg,rgba(238,132,34,0) 0%,rgba(190,110,40,.25) 45%,rgba(238,132,34,0) 80%)" role="img" aria-label="Faded photo of a senior man using a tablet"></div>
  <h2>FIND AN ADVISOR NEAR YOU</h2>
  <div class="field"><svg width="11" height="15" viewBox="0 0 12 16"><path d="M6 0a6 6 0 0 0-6 6c0 4.5 6 10 6 10s6-5.5 6-10a6 6 0 0 0-6-6zm0 8.5A2.5 2.5 0 1 1 6 3.5a2.5 2.5 0 0 1 0 5z" fill="#666"/></svg>Enter city or postal code</div>
  <span class="btn-blue">SEARCH</span>
  <svg class="abs" style="left:0;top:0" width="1200" height="660" viewBox="0 0 1200 660">
    <path d="M0,440 Q600,100 1200,440 L1200,660 L0,660 Z" fill="#fff"/>
    <path d="M0,440 Q600,100 1200,440" fill="none" stroke="#0b72ae" stroke-width="12"/>
  </svg>
</section>

<footer>
  <div class="abs social"><span></span><span></span><span></span><span></span></div>
  <div class="abs contact">
    <svg width="10" height="14" viewBox="0 0 12 16"><path d="M6 0a6 6 0 0 0-6 6c0 4.5 6 10 6 10s6-5.5 6-10a6 6 0 0 0-6-6zm0 8.5A2.5 2.5 0 1 1 6 3.5a2.5 2.5 0 0 1 0 5z" fill="#ee8422"/></svg>
    Totam rem aperiam, eaque ip &nbsp;|&nbsp;
    <svg width="13" height="13" viewBox="0 0 24 24"><path d="M6.6 10.8a15 15 0 0 0 6.6 6.6l2.2-2.2a1 1 0 0 1 1-.25 11.4 11.4 0 0 0 3.6.57 1 1 0 0 1 1 1V20a1 1 0 0 1-1 1A17 17 0 0 1 3 4a1 1 0 0 1 1-1h3.5a1 1 0 0 1 1 1c0 1.25.2 2.45.57 3.57a1 1 0 0 1-.25 1z" fill="#ee8422"/></svg>
    1 800 555 0142 &nbsp;|&nbsp;
    <svg width="16" height="12" viewBox="0 0 16 12"><rect width="16" height="12" rx="1" fill="#ee8422"/><path d="M1 1l7 5 7-5" fill="none" stroke="#fff" stroke-width="1.5"/></svg>
    &nbsp;hello@theeldernook.com
  </div>
  <nav class="abs links"><span>Help</span><span>|</span><span>FAQ</span><span>|</span><span>Support</span><span>|</span><span>Sitemap</span><span>|</span><span>Terms Of Use</span><span>|</span><span>Privacy Statement</span></nav>
  <p class="abs copy">The Elder Nook © 2019 All rights reserved.</p>
</footer>

</body>
</html>
```